Thornvale Group needs a business card design

We need a new business card design using the logo recently selected in a logo competition on Pixel Bazaar. Our business is a consultancy specializing in aviation and energy and the winning business card design will promote an image of precision and professionalism with creativity.

Please use the logo with the name on the front of the card and use a complementary font. Make the back white with either the light grey or dark grey logo.

Target Market(s)

Senior finance and legal leaders at aviation and energy companies

Industry/Entity Type

Management Consulting

Contact Information for Business Card

Peter Castrell
President
Thornvale Group

www.thornvalegroup.example

(555) 204-6391
pc@thornvalegroup.example

Requirements
Must have
• Professional font that goes well with the logo font

```html
<!DOCTYPE html>
<html lang="en">
<head>
<meta charset="utf-8">
<title>Thornvale Group — Business Card</title>
<link rel="stylesheet" href="https://fonts.googleapis.com/css2?family=Source+Sans+3:wght@400;600&display=swap">
<style>
  :root {
    --navy: #0f4273;
    --navy-line: rgba(255,255,255,0.22);
    --paper: #ffffff;
    --stage: #e8e6e3;
    --ink-white: #ffffff;
  }
  * { margin: 0; padding: 0; box-sizing: border-box; }
  html, body { width: 1200px; height: 900px; overflow: hidden; }
  body {
    background: var(--stage);
    font-family: "Source Sans 3", "Helvetica Neue", Arial, sans-serif;
    position: relative;
  }
  .card {
    position: absolute;
    background: var(--paper);
    box-shadow: 0 6px 18px rgba(0,0,0,0.18);
    overflow: hidden;
  }

  /* Shared brand lockup: name plus one plain square */
  .brand {
    display: flex; align-items: center; gap: 12px;
    font-weight: 400; line-height: 1; letter-spacing: 1.5px;
    white-space: nowrap;
  }
  .brand-mark { flex: none; }

  /* Front */
  .card-front { left: 77px; top: 35px; width: 589px; height: 363px; }
  .front-brand {
    position: absolute; left: 31px; top: 88px;
    color: var(--navy);
  }
  .front-brand .brand-name { font-size: 24px; }
  .front-brand .brand-mark { width: 14px; height: 14px; background: var(--navy); }

  .front-band {
    position: absolute; left: 0; top: 155px; width: 100%; height: 208px;
    background: var(--navy); color: var(--ink-white);
  }
  .contact-list { position: absolute; left: 32px; top: 0; width: 216px; }
  .contact-name {
    font-size: 22px; font-weight: 600; height: 64px;
    display: flex; align-items: center;
    border-bottom: 1px solid var(--navy-line);
  }
  .contact-row {
    font-size: 16px; font-weight: 400; height: 41px;
    display: flex; align-items: center; gap: 16px;
    border-bottom: 1px solid var(--navy-line);
    white-space: nowrap;
  }
  .contact-row:last-child { border-bottom: none; height: 34px; font-size: 15px; }
  .contact-row svg { width: 12px; height: 12px; flex: none; }

  /* Back */
  .card-back { left: 388px; top: 505px; width: 567px; height: 352px; }
  .back-band {
    position: absolute; left: 0; top: 110px; width: 100%; height: 131px;
    background: var(--navy); color: var(--ink-white);
    display: flex; align-items: center; justify-content: center;
  }
  .back-band .brand { gap: 18px; }
  .back-band .brand-name { font-size: 40px; letter-spacing: 2px; }
  .back-band .brand-mark { width: 22px; height: 22px; background: var(--ink-white); }
</style>
</head>
<body>
  <section class="card card-front">
    <div class="brand front-brand">
      <span class="brand-mark"></span>
      <span class="brand-name">THORNVALE GROUP</span>
    </div>
    <div class="front-band">
      <div class="contact-list">
        <div class="contact-name">Peter Castrell</div>
        <div class="contact-row">President</div>
        <div class="contact-row">
          <svg viewBox="0 0 12 12" aria-hidden="true"><path fill="#fff" d="M2.4 0.8 4.2 3 3.3 4.3c.7 1.6 2.1 3 3.8 3.8L8.4 7.2 10.6 9 9.6 11C5 10.5 1.3 6.8 0.8 2.2Z"/></svg>
          <span>(555) 204-6391</span>
        </div>
        <div class="contact-row">
          <svg viewBox="0 0 12 12" aria-hidden="true"><rect x="0.5" y="2.5" width="11" height="7.5" fill="#fff"/><path d="M0.8 2.8 6 6.8 11.2 2.8" stroke="#0f4273" stroke-width="1" fill="none"/></svg>
          <span>pc@thornvalegroup.example</span>
        </div>
      </div>
    </div>
  </section>

  <section class="card card-back">
    <div class="back-band">
      <div class="brand">
        <span class="brand-mark"></span>
        <span class="brand-name">THORNVALE GROUP</span>
      </div>
    </div>
  </section>
</body>
</html>
```